Agriculture Business Card

I want to use my existing logo and use my tagline of "Don't Guess...Soil Test" on the card. Looking for a double sided card that will really get peoples attention.
Contact Info:
Marlow Field Crop Edge
Calvin Brusk
2917 K Lane
Larkin, NE 68593
402-555-0193
calvin.r.brusk@fieldmailbox.net

```html
<!DOCTYPE html>
<html lang="en">
<head>
<meta charset="utf-8">
<title>Marlow Field Crop Edge – Business Card</title>
<link rel="stylesheet" href="https://fonts.googleapis.com/css2?family=Fira+Sans+Extra+Condensed:wght@600&family=Michroma&family=Roboto:wght@400;500&display=swap">
<style>
  :root {
    --stage: #2a2a2a;
    --soil: #a26c4e;
    --paper: #ffffff;
    --harvest: #f8b21b;
    --leaf: #5fbf45;
    --ink: #2b2b2b;
    --brown-text: #9a6646;
  }
  * { margin: 0; padding: 0; box-sizing: border-box; }
  html, body { width: 1200px; height: 1015px; overflow: hidden; }
  body {
    background: var(--stage);
    display: flex;
    flex-direction: column;
    align-items: center;
    justify-content: center;
    gap: 50px;
  }
  .card {
    width: 760px;
    height: 434px;
    position: relative;
    overflow: hidden;
  }

  /* Front side */
  .card-front {
    background: var(--soil);
    display: flex;
    flex-direction: column;
    align-items: center;
    justify-content: center;
  }
  .brand {
    display: flex;
    align-items: center;
    gap: 18px;
  }
  .brand-dot {
    width: 64px;
    height: 64px;
    border-radius: 50%;
    background: var(--harvest);
  }
  .brand-name {
    font-family: "Fira Sans Extra Condensed", sans-serif;
    font-weight: 600;
    font-size: 46px;
    line-height: 1.0;
    color: var(--paper);
    text-align: center;
  }
  .tagline {
    margin-top: 54px;
    font-family: "Michroma", sans-serif;
    font-size: 24px;
    letter-spacing: 2px;
    color: var(--harvest);
  }

  /* Back side */
  .card-back {
    background: var(--paper);
  }
  .contact {
    position: absolute;
    left: 58px;
    top: 118px;
    font-family: "Roboto", sans-serif;
  }
  .person-name {
    font-weight: 500;
    font-size: 38px;
    color: var(--brown-text);
    margin-bottom: 22px;
  }
  .contact-line {
    display: flex;
    align-items: center;
    gap: 10px;
    font-size: 20px;
    color: var(--ink);
    line-height: 1.35;
  }
  .contact-line svg { width: 18px; height: 18px; flex: none; }
  .company {
    margin-top: 24px;
    font-size: 22px;
    color: var(--brown-text);
    line-height: 1.2;
  }
  .address {
    font-size: 21px;
    color: var(--ink);
    line-height: 1.25;
  }
  .brand-mark-large {
    position: absolute;
    right: 0;
    top: 0;
    width: 300px;
    height: 100%;
    display: flex;
    align-items: center;
    justify-content: center;
    border-left: 14px solid var(--leaf);
  }
  .brand-mark-large span {
    font-family: "Fira Sans Extra Condensed", sans-serif;
    font-weight: 600;
    font-size: 44px;
    line-height: 1.05;
    color: var(--harvest);
    text-align: center;
  }
</style>
</head>
<body>

  <section class="card card-front">
    <div class="brand">
      <div class="brand-dot"></div>
      <div class="brand-name">Marlow Field Crop<br>Edge</div>
    </div>
    <p class="tagline">DON'T GUESS...SOIL TEST</p>
  </section>

  <section class="card card-back">
    <div class="contact">
      <h1 class="person-name">Calvin Brusk</h1>
      <p class="contact-line">
        <svg viewBox="0 0 24 24" aria-hidden="true"><path fill="var(--brown-text)" d="M6.6 10.8a15.1 15.1 0 0 0 6.6 6.6l2.2-2.2c.3-.3.7-.4 1-.2 1.1.4 2.3.6 3.6.6.6 0 1 .4 1 1V20c0 .6-.4 1-1 1A17 17 0 0 1 3 4c0-.6.4-1 1-1h3.5c.6 0 1 .4 1 1 0 1.3.2 2.5.6 3.6.1.3 0 .7-.2 1z"/></svg>
        402-555-0193
      </p>
      <p class="contact-line">
        <svg viewBox="0 0 24 24" aria-hidden="true"><path fill="var(--brown-text)" d="M2 5h20v14H2zm2 2v.5l8 5 8-5V7l-8 5z"/></svg>
        calvin.r.brusk@fieldmailbox.net
      </p>
      <p class="company">Marlow Field Crop<br>Edge</p>
      <p class="address">2917 K Lane<br>Larkin, NE 68593</p>
    </div>
    <div class="brand-mark-large">
      <span>Marlow Field<br>Crop Edge</span>
    </div>
  </section>

</body>
</html>
```